Gobal construction supply company needs new business card design

I need a business card design for my global supply company using an existing logo. i will be looking to print these on rounded corner cards with the black background version of my logo on the back. on the front white background, my logo again and my simple details.

```html
<!DOCTYPE html>
<html lang="en">
<head>
<meta charset="UTF-8">
<title>Northgate Build Supply – Business Cards</title>
<link rel="stylesheet" href="https://fonts.googleapis.com/css2?family=Montserrat:wght@700&family=Work+Sans:wght@400;500&display=swap">
<style>
  :root {
    --backdrop: #2a2a2a;
    --card-dark: #1c1c1c;
    --card-dark-edge: #262626;
    --card-light: #ffffff;
    --ink: #1c1c1c;
    --ink-soft: #4a4a4a;
    --white: #ffffff;
    --red: #d71f26;
  }
  * { margin: 0; padding: 0; box-sizing: border-box; }
  html, body { width: 1200px; height: 900px; overflow: hidden; }
  body {
    background: var(--backdrop);
    font-family: "Work Sans", Arial, sans-serif;
    position: relative;
  }
  .card {
    position: absolute;
    left: 250px;
    width: 700px;
    height: 400px;
    border-radius: 18px;
    box-shadow: 0 10px 30px rgba(0,0,0,.45);
  }
  .card--back {
    top: 40px;
    background: linear-gradient(135deg, var(--card-dark) 0%, var(--card-dark-edge) 100%);
  }
  .card--front {
    top: 470px;
    background: var(--card-light);
  }

  .brand {
    font-family: "Montserrat", Arial, sans-serif;
    font-weight: 700;
    text-transform: uppercase;
    letter-spacing: 1px;
    white-space: nowrap;
  }

  /* Back: dark, name centred */
  .card--back .brand {
    position: absolute;
    left: 0; right: 0; top: 172px;
    text-align: center;
    font-size: 30px;
    color: var(--white);
  }
  .back-rule {
    position: absolute;
    left: 190px; right: 190px; top: 228px;
    height: 2px;
    background: var(--red);
  }

  /* Front: white, details */
  .card--front .brand--small {
    position: absolute;
    left: 46px; top: 38px;
    font-size: 19px;
    color: var(--ink);
  }
  .front-rule {
    position: absolute;
    left: 46px; top: 72px;
    width: 270px; height: 2px;
    background: var(--red);
  }
  .person { position: absolute; left: 46px; top: 104px; }
  .person__name {
    font-size: 26px;
    font-weight: 500;
    color: var(--red);
    text-transform: uppercase;
    letter-spacing: .5px;
  }
  .person__title { font-size: 17px; color: var(--ink-soft); margin-top: 2px; }

  .address {
    position: absolute; left: 46px; top: 196px;
    font-size: 17px; line-height: 25px; color: var(--ink);
    font-style: normal; letter-spacing: .8px;
  }
  .contacts {
    position: absolute; left: 46px; top: 270px;
    list-style: none;
    font-size: 17px; line-height: 27px; color: var(--ink);
    letter-spacing: .8px;
  }
  .contacts li { display: flex; align-items: center; gap: 10px; }
  .contacts svg { width: 12px; height: 12px; flex: none; }

  .card--front .brand--large {
    position: absolute;
    right: 50px; top: 210px;
    font-size: 40px;
    letter-spacing: 0;
    color: var(--ink);
  }
</style>
</head>
<body>
  <section class="card card--back" aria-label="Card back">
    <p class="brand">Northgate Build Supply</p>
    <div class="back-rule"></div>
  </section>

  <section class="card card--front" aria-label="Card front">
    <p class="brand brand--small">Northgate Build Supply</p>
    <div class="front-rule"></div>

    <div class="person">
      <p class="person__name">Daniel Hartley</p>
      <p class="person__title">Director</p>
    </div>

    <address class="address">48 Ridge Road Box<br>2210, Pine Falls, AB</address>

    <ul class="contacts">
      <li>
        <svg viewBox="0 0 12 12" aria-hidden="true"><path d="M2.5 1 L4.5 1 L5 3.5 L3.8 4.4 Q5 7 7.6 8.2 L8.5 7 L11 7.5 L11 9.5 Q11 11 9.5 11 Q1 10 1 2.5 Q1 1 2.5 1 Z" fill="var(--red)"/></svg>
        <span>403-555-0182</span>
      </li>
      <li>
        <svg viewBox="0 0 12 12" aria-hidden="true"><rect x="1" y="2.5" width="10" height="7" fill="none" stroke="var(--red)" stroke-width="1.2"/><path d="M1 2.5 L6 6.5 L11 2.5" fill="none" stroke="var(--red)" stroke-width="1.2"/></svg>
        <span>info@northgatesupply.com</span>
      </li>
      <li>
        <svg viewBox="0 0 12 12" aria-hidden="true"><circle cx="6" cy="6" r="5" fill="none" stroke="var(--red)" stroke-width="1.2"/><ellipse cx="6" cy="6" rx="2.2" ry="5" fill="none" stroke="var(--red)" stroke-width="1"/><path d="M1 6 H11" stroke="var(--red)" stroke-width="1"/></svg>
        <span>www.northgatesupply.com</span>
      </li>
    </ul>

    <p class="brand brand--large">Northgate</p>
  </section>
</body>
</html>
```